Animal Eye Clinic needs a Business card

We are a new veterinary ophthalmology practice (Ridgeline Pet Vision Care) and we need a business card designed. We only see animal eyes - we are not a regular veterinary clinic. We already have a logo. We are looking for a professional, good looking business card to hand out to our clients. We are looking for something simple but professional and contemporary. Our logo is likely the only picture/graphic that needs to be on the card.
Updates

Contact Information for Business Card

Delia Vossman, BSc, DVM, MSc, DipACVO
Veterinary Ophthalmologist

Phone: 250.418.3927
Email: ridgelinepetvisioncare@mailbox-example.net
Website: ridgelinepetvisioncare-example.net
Address: 1874 Thornbury Rd
Kelowna, BC, V1X 4M9

Colors

Designer to choose colors to be used in the design.

Requirements
Must have
• Our logo (attached)

```html
<!DOCTYPE html>
<html lang="en">
<head>
<meta charset="utf-8">
<title>Ridgeline Pet Vision Care – Business Card</title>
<link rel="stylesheet" href="https://fonts.googleapis.com/css2?family=Roboto:wght@400;500;700&display=swap">
<style>
  :root {
    --page-bg: #e6e3df;
    --card-light: #f4f5f6;
    --card-mid: #e4e8ea;
    --teal: #1e6f7b;
    --teal-deep: #0f5866;
    --charcoal: #3b3d40;
    --text-grey: #4a4c4f;
    --rule-white: #ffffff;
  }
  * { box-sizing: border-box; margin: 0; padding: 0; }
  html, body { width: 1200px; height: 970px; overflow: hidden; }
  body {
    background: var(--page-bg);
    font-family: "Roboto", Arial, sans-serif;
    position: relative;
  }
  .business-card {
    position: absolute;
    left: 80px;
    top: 189px;
    width: 1040px;
    height: 592px;
    overflow: hidden;
    box-shadow: 0 10px 30px rgba(0,0,0,0.15);
  }
  .card-shapes { position: absolute; inset: 0; width: 100%; height: 100%; }
  .brand {
    position: absolute;
    left: 58px;
    top: 112px;
    display: flex;
    align-items: center;
    gap: 22px;
  }
  .brand-dot {
    width: 84px; height: 84px;
    border-radius: 50%;
    background: var(--teal);
  }
  .brand-name {
    font-size: 41px;
    font-weight: 700;
    color: var(--teal);
    letter-spacing: -0.3px;
  }
  .person { position: absolute; left: 57px; top: 290px; }
  .person-line { font-size: 31px; color: var(--teal); letter-spacing: -0.2px; }
  .person-name { font-weight: 700; }
  .person-credentials { font-weight: 400; }
  .person-role { font-size: 22px; color: var(--text-grey); margin-top: 6px; }
  .contact-list {
    position: absolute;
    left: 58px;
    top: 400px;
    list-style: none;
  }
  .contact-item {
    display: flex;
    align-items: center;
    gap: 12px;
    height: 37px;
    font-size: 22px;
    color: var(--text-grey);
  }
  .contact-icon { width: 22px; height: 22px; flex: none; }
</style>
</head>
<body>
  <article class="business-card">
    <svg class="card-shapes" viewBox="0 0 1040 592" preserveAspectRatio="none" aria-hidden="true">
      <defs>
        <linearGradient id="cardFace" x1="0" y1="0" x2="1" y2="1">
          <stop offset="0" stop-color="var(--card-light)"/>
          <stop offset="1" stop-color="var(--card-mid)"/>
        </linearGradient>
        <linearGradient id="tealBand" x1="0" y1="0" x2="0" y2="1">
          <stop offset="0" stop-color="var(--teal)"/>
          <stop offset="1" stop-color="var(--teal-deep)"/>
        </linearGradient>
      </defs>
      <rect class="band-teal" x="0" y="0" width="1040" height="592" fill="url(#tealBand)"/>
      <path class="card-face" d="M0 0 H840 Q1020 296 840 592 H0 Z" fill="url(#cardFace)"/>
      <path class="sweep-charcoal" d="M660 0 H858 Q942 130 928 300 Q880 80 660 0 Z" fill="var(--charcoal)" stroke="var(--rule-white)" stroke-width="3"/>
    </svg>

    <div class="brand">
      <span class="brand-dot"></span>
      <span class="brand-name">Ridgeline Pet Vision Care</span>
    </div>

    <div class="person">
      <p class="person-line"><span class="person-name">Delia Vossman</span><span class="person-credentials">, BSc, DVM, MSc, DipACVO</span></p>
      <p class="person-role">Veterinary Ophthalmologist</p>
    </div>

    <ul class="contact-list">
      <li class="contact-item">
        <svg class="contact-icon" viewBox="0 0 24 24" aria-hidden="true"><rect x="6" y="2" width="12" height="20" rx="2" fill="none" stroke="var(--teal)" stroke-width="2.2"/><circle cx="12" cy="18.5" r="1.2" fill="var(--teal)"/></svg>
        <span>250.418.3927</span>
      </li>
      <li class="contact-item">
        <svg class="contact-icon" viewBox="0 0 24 24" aria-hidden="true"><rect x="2" y="5" width="20" height="14" fill="var(--teal)"/><path d="M2 5 L12 13 L22 5" fill="none" stroke="#fff" stroke-width="1.6"/></svg>
        <span>ridgelinepetvisioncare@mailbox-example.net</span>
      </li>
      <li class="contact-item">
        <svg class="contact-icon" viewBox="0 0 24 24" aria-hidden="true"><circle cx="12" cy="12" r="10" fill="var(--teal)"/><g fill="none" stroke="#fff" stroke-width="1.2"><ellipse cx="12" cy="12" rx="4.5" ry="10"/><path d="M2 12 H22 M4 7 H20 M4 17 H20"/></g></svg>
        <span>ridgelinepetvisioncare-example.net</span>
      </li>
      <li class="contact-item">
        <svg class="contact-icon" viewBox="0 0 24 24" aria-hidden="true"><path d="M12 2 C7.6 2 5 5.2 5 9 C5 14 12 22 12 22 C12 22 19 14 19 9 C19 5.2 16.4 2 12 2 Z" fill="var(--teal)"/><circle cx="12" cy="9" r="2.6" fill="#fff"/></svg>
        <span>1874 Thornbury Rd, Kelowna, BC, V1X 4M9</span>
      </li>
    </ul>
  </article>
</body>
</html>
```